High-end construction company needs a business card design

We need a modern looking business card that draws people in, is memorable and looks so good people will want to sick it on their fridges.
On the first side what is needed are:
Logo
My name - Tomasz Brelwik
Title - Managing Director
Website - www.varkelt.co.uk
Email - tomasz@varkelt.co.uk
Telephone - 020 5194 6281
Mobile - 07845139072
On the back side was is needed is a list of all the services we provide:
-Kitchen Renovations
-Bathroom Renovations
-House Renovations
-Garage Conversions
-Extensions
-Loft Conversions
-Conservatories
-Carpentry
-Tiling
-Electrical
-Plumbing & Heating
-Bricklaying
-Landscaping
-Decorating
-Plastering
We would like the colours to be the same shades as on the logo with grey or black for the words.
Target Market(s)
Anyone who needs building work done
Contact Information for Business Card
This business card is for a construction company which strives to deliver excellent service and quality.
The look and feel of the card should represent this.
Requirements
Must have
- On the first side what is needed are:
Logo
My name - Tomasz Brelwik
Title - Managing Director
Website - www.varkelt.co.uk
Email - tomasz@varkelt.co.uk
Telephone - 020 5194 6281
Mobile - 07845139072
Nice to have
- Cool looking features

```html
<!DOCTYPE html>
<html lang="en">
<head>
<meta charset="utf-8">
<title>Varkelt Construction Ltd – Business Card</title>
<link rel="stylesheet" href="https://fonts.googleapis.com/css2?family=Archivo:wght@400;500;700;800&display=swap">
<style>
  :root {
    --page-bg: #e6e8e5;
    --card-white: #fbfbf9;
    --green-deep: #3f8a3a;
    --green-mid: #4a9a40;
    --green-bright: #6cc24a;
    --green-faint: #58a84d;
    --ink-grey: #4a4a4a;
    --text-white: #ffffff;
  }
  * { box-sizing: border-box; margin: 0; padding: 0; }
  html, body {
    width: 1200px; height: 896px; overflow: hidden;
    background: var(--page-bg);
    font-family: "Archivo", Arial, sans-serif;
  }
  .sheet {
    width: 1200px; height: 896px;
    display: flex; align-items: center; justify-content: center; gap: 40px;
  }
  .card {
    width: 540px; height: 309px; position: relative; overflow: hidden;
    box-shadow: 0 10px 28px rgba(0,0,0,.18);
  }

  /* Back: services */
  .card-back {
    background: linear-gradient(135deg, var(--green-mid), var(--green-deep));
    color: var(--text-white);
  }
  .back-brand {
    position: absolute; left: 40px; top: 58px; width: 220px;
    font-weight: 800; font-size: 46px; line-height: .95; letter-spacing: 1px;
    color: var(--green-faint); text-transform: uppercase;
  }
  .back-brand span { display: block; font-size: 17px; letter-spacing: 3px; margin-top: 8px; }
  .back-rule {
    position: absolute; left: 40px; right: 40px; top: 178px; height: 1px;
    background: linear-gradient(90deg, transparent, var(--green-bright), transparent);
  }
  .services-title {
    position: absolute; left: 0; right: 0; top: 158px; text-align: center;
    font-weight: 700; font-size: 17px; letter-spacing: .5px;
  }
  .services-title span { background: var(--green-mid); padding: 0 12px; }
  .services-list {
    position: absolute; left: 24px; right: 24px; top: 196px;
    list-style: none; text-align: center;
    font-size: 13.5px; line-height: 21px;
  }
  .services-list li { display: inline; white-space: nowrap; }
  .services-list li::before {
    content: ""; display: inline-block; width: 5px; height: 5px; border-radius: 50%;
    background: var(--green-bright); margin: 0 5px 2px 6px; vertical-align: middle;
  }

  /* Front: contact */
  .card-front { background: var(--card-white); }
  .front-band {
    position: absolute; left: 0; right: 0; bottom: 0; height: 14px;
    background: linear-gradient(90deg, var(--green-bright), var(--green-deep));
  }
  .front-brand {
    position: absolute; left: 34px; top: 108px; width: 210px;
    font-weight: 800; font-size: 40px; line-height: 1; color: var(--green-bright);
    text-transform: uppercase; letter-spacing: 1px;
  }
  .front-brand .brand-sub { display: block; font-size: 15px; letter-spacing: 2.5px; margin-top: 6px; }
  .front-divider {
    position: absolute; left: 262px; top: 60px; width: 1px; height: 176px;
    background: var(--green-bright);
  }
  .contact { position: absolute; left: 290px; top: 62px; color: var(--ink-grey); }
  .contact-name {
    font-weight: 700; font-size: 22px; color: var(--green-deep);
    text-transform: uppercase; letter-spacing: .3px;
  }
  .contact-title { font-size: 15px; margin-top: 3px; }
  .contact-list { list-style: none; margin-top: 26px; font-size: 14.5px; line-height: 24px; }
  .contact-list li { display: flex; align-items: center; gap: 8px; }
  .contact-list svg { width: 13px; height: 13px; fill: var(--green-deep); flex: none; }
</style>
</head>
<body>
<main class="sheet">

  <section class="card card-back" aria-label="Card back – services">
    <div class="back-brand">Varkelt<span>Construction Ltd</span></div>
    <div class="back-rule"></div>
    <h2 class="services-title"><span>SERVICES</span></h2>
    <ul class="services-list">
      <li>Kitchen Renovations</li> <li>Bathroom Renovations</li> <li>House Renovations</li>
      <li>Garage Conversions</li> <li>Extensions</li> <li>Loft Conversions</li> <li>Conservatories</li>
      <li>Carpentry</li> <li>Tiling</li> <li>Electrical</li> <li>Plumbing &amp; Heating</li>
      <li>Bricklaying</li> <li>Landscaping</li> <li>Decorating</li> <li>Plastering</li>
    </ul>
  </section>

  <section class="card card-front" aria-label="Card front – contact details">
    <div class="front-brand">Varkelt<span class="brand-sub">Construction Ltd</span></div>
    <div class="front-divider"></div>
    <div class="contact">
      <h1 class="contact-name">Tomasz Brelwik</h1>
      <p class="contact-title">Managing Director</p>
      <ul class="contact-list">
        <li><svg viewBox="0 0 24 24" aria-hidden="true"><path d="M6.6 10.8a15 15 0 0 0 6.6 6.6l2.2-2.2a1 1 0 0 1 1-.25 11.4 11.4 0 0 0 3.6.57 1 1 0 0 1 1 1V20a1 1 0 0 1-1 1A17 17 0 0 1 3 4a1 1 0 0 1 1-1h3.5a1 1 0 0 1 1 1c0 1.25.2 2.45.57 3.6a1 1 0 0 1-.25 1z"/></svg>020 5194 6281</li>
        <li><svg viewBox="0 0 24 24" aria-hidden="true"><path d="M7 1h10a2 2 0 0 1 2 2v18a2 2 0 0 1-2 2H7a2 2 0 0 1-2-2V3a2 2 0 0 1 2-2zm0 3v14h10V4zm5 15.5a1 1 0 1 0 0 2 1 1 0 0 0 0-2z"/></svg>07845139072</li>
        <li><svg viewBox="0 0 24 24" aria-hidden="true"><path d="M2 5h20v14H2zm2 2v.5l8 5 8-5V7zm0 2.8V17h16V9.8l-8 5z"/></svg>tomasz@varkelt.co.uk</li>
        <li><svg viewBox="0 0 24 24" aria-hidden="true"><path d="M12 2a10 10 0 1 0 0 20 10 10 0 0 0 0-20zm6.9 6h-2.9a15 15 0 0 0-1.4-3.6A8 8 0 0 1 18.9 8zM12 4c.8 1.2 1.5 2.5 1.9 4h-3.8c.4-1.5 1.1-2.8 1.9-4zM4.3 14a8 8 0 0 1 0-4h3.4a16 16 0 0 0 0 4zm.8 2h2.9c.3 1.3.8 2.5 1.4 3.6A8 8 0 0 1 5.1 16zM8 8H5.1a8 8 0 0 1 4.3-3.6C8.8 5.5 8.3 6.7 8 8zm4 12c-.8-1.2-1.5-2.5-1.9-4h3.8c-.4 1.5-1.1 2.8-1.9 4zm2.3-6H9.7a14 14 0 0 1 0-4h4.6a14 14 0 0 1 0 4zm.3 5.6c.6-1.1 1.1-2.3 1.4-3.6h2.9a8 8 0 0 1-4.3 3.6zm1.7-5.6a16 16 0 0 0 0-4h3.4a8 8 0 0 1 0 4z"/></svg>www.varkelt.co.uk</li>
      </ul>
    </div>
    <div class="front-band"></div>
  </section>

</main>
</body>
</html>
```